Halvern Studio Works New Business Card

I am opening a new division of my business. I am a high end interior designer, and the new business is writing specs for construction projects. It will be marketed to the VERY high end contractor, architects and realtors. The client will actually be the one who pays us and signs the agreement, but it will be the contractor, architect or realtor that will recommend us. I have attached my current card and our previous logo which is still used on some of our paperwork. I would like the new logo to be connected in some way to what we are currently using. We will need to have room on the card for a person's name. I'd like to omit the address as we might be moving the office soon. The web address is www.HalvernStudioWorks.com. For this design, please use my name, Marisol Thornbury.

Target Market(s)

High End Luxury Contractors, Realtors and Architects

Industry/Entity Type

Residential Construction

Contact Information for Business Card

Halvern Studio Works, Phone: 555-214-9087, www.HalvernStudioWorks.com , Marisol Thornbury

Font styles to use
Sans Serif

Colors
ec1f27

Requirements
Must have
• Some visual reference to my current card and logos. Use the colors submitted on the business card I attached.
Nice to have
• A visual reference to my current card and logos. Use the colors submitted on the card I attached.
Should not have
• A physical address

```html
<!DOCTYPE html>
<html lang="en">
<head>
<meta charset="utf-8">
<title>Marisol Thornbury – Business Card</title>
<link rel="stylesheet" href="https://fonts.googleapis.com/css2?family=Open+Sans:wght@400;600&display=swap">
<style>
  :root {
    --backdrop: #e9e6e2;
    --card: #ffffff;
    --rust: #983a24;
    --name-rust: #8a2f1c;
    --grey-text: #5f5f5f;
    --logo-grey: #7a7a7a;
    --shadow: rgba(0, 0, 0, 0.28);
  }
  * { margin: 0; padding: 0; box-sizing: border-box; }
  html, body {
    width: 1200px;
    height: 1000px;
    overflow: hidden;
    background: var(--backdrop);
    font-family: "Open Sans", Arial, sans-serif;
  }
  .canvas { position: relative; width: 1200px; height: 1000px; }

  .card {
    position: absolute;
    left: 265px;
    width: 666px;
    height: 397px;
    background: var(--card);
    box-shadow: 0 3px 8px var(--shadow);
  }
  .card--front { top: 73px; }
  .card--back { top: 533px; }

  /* Brand lockup: plain square + name */
  .brand { position: absolute; text-align: center; }
  .brand__square { display: block; margin: 0 auto; background: var(--rust); }
  .brand__name {
    display: block;
    color: var(--logo-grey);
    font-weight: 400;
    text-transform: uppercase;
    white-space: nowrap;
  }

  .card--front .brand { left: 28px; top: 139px; width: 330px; }
  .card--front .brand__square { width: 97px; height: 56px; }
  .card--front .brand__name { margin-top: 14px; font-size: 21px; letter-spacing: 2px; }

  .card--back .brand { left: 0; top: 114px; width: 666px; }
  .card--back .brand__square { width: 133px; height: 77px; }
  .card--back .brand__name { margin-top: 20px; font-size: 33px; letter-spacing: 3px; }

  /* Contact block */
  .contact { position: absolute; left: 365px; top: 133px; }
  .contact__person {
    color: var(--name-rust);
    font-weight: 600;
    font-size: 17px;
    letter-spacing: 0.3px;
    text-transform: uppercase;
    margin-bottom: 36px;
  }
  .contact__list { list-style: none; }
  .contact__item {
    display: flex;
    align-items: center;
    gap: 7px;
    color: var(--grey-text);
    font-size: 15.5px;
    line-height: 24px;
  }
  .contact__icon { width: 14px; height: 14px; flex: none; fill: var(--name-rust); }
</style>
</head>
<body>
<main class="canvas">

  <section class="card card--front" aria-label="Card front">
    <div class="brand">
      <span class="brand__square"></span>
      <span class="brand__name">Marisol Thornbury</span>
    </div>

    <div class="contact">
      <p class="contact__person">Marisol Thornbury</p>
      <ul class="contact__list">
        <li class="contact__item">
          <svg class="contact__icon" viewBox="0 0 14 14" aria-hidden="true">
            <path d="M1 5c0-2 3-3 6-3s6 1 6 3v1h-3V4.5C9 4 5 4 4 4.5V6H1z"/>
            <path d="M4 7h6l2 5H2z"/>
          </svg>
          555.214.9087
        </li>
        <li class="contact__item">
          <svg class="contact__icon" viewBox="0 0 14 14" aria-hidden="true">
            <path d="M1 3h12v1L7 8 1 4z"/>
            <path d="M1 5.5l6 4 6-4V11H1z"/>
          </svg>
          marisol@halvernstudioworks.com
        </li>
        <li class="contact__item">
          <svg class="contact__icon" viewBox="0 0 14 14" aria-hidden="true">
            <path d="M1 2h12v8H1zM2.5 3.5v5h9v-5z"/>
            <path d="M5 11h4v1H5z"/>
          </svg>
          www.halvernstudioworks.com
        </li>
      </ul>
    </div>
  </section>

  <section class="card card--back" aria-label="Card back">
    <div class="brand">
      <span class="brand__square"></span>
      <span class="brand__name">Marisol Thornbury</span>
    </div>
  </section>

</main>
</body>
</html>
```